Website for Dental Office - The Bright Arch Clinic

The bright arch clinic is a dental office offering cosmetic dentistry, general dentistry, and multi-specialty dental care all under one roof in our state-of-the-art cosmetic dental center. We are particularly striving to provide services that fit the need of the young generation. Thus, we hope to have a modern, professional concise website that represents our spirit.

*Should be able to switch from English to Chinese

6 sections besides homepage:
Home, Meet us, Services,
Patient Info, Cases&Reviews, Blog, Contact

The Services sections should contain multiple subsections such as cleaning and prevention, cosmetic dentistry, implant dentistry, removable dentures, etc...
The Patient Info section is also intended to contain several subsections such as
New Patient offer, accepted Insurance, patient portal, helpful tips, etc...

Target Market(s)

young generation

Coding

Coded - Design and coding required

Number of Pages Required

5+ page

Font styles to use
Sans Serif

Colors
0592cd
33a6d7
85cae6
00a990
33b8a4
86cfc6
cee9f5
cfeae6
3277b5

Requirements
Must have
• *Should be able to switch from English to Chinese
Nice to have
• http://www.thebrightarchclinic.com/
• As a reference, the above link is the current website, but we would like to change the appearance and the content (our new logo's picture is attached)

```html
<!DOCTYPE html>
<html lang="en">
<head>
<meta charset="utf-8">
<title>The Bright Arch Clinic</title>
<link rel="stylesheet" href="https://fonts.googleapis.com/css2?family=Cabin:wght@400;500;600;700&family=Lato:wght@300;400;700&display=swap">
<style>
:root{
  --blue:#0592cd;
  --blue-mid:#33a6d7;
  --blue-soft:#85cae6;
  --blue-pale:#cee9f5;
  --teal:#00a990;
  --teal-mid:#33b8a4;
  --teal-pale:#cfeae6;
  --deep:#3277b5;
  --ink:#333;
  --muted:#8a8a8a;
  --line:#e3e3e3;
  --topbar:#1b1b1b;
  --grey-bg:#f4f4f4;
}
*{box-sizing:border-box;margin:0;padding:0}
html,body{width:1200px;height:4135px;overflow:hidden}
body{font-family:"Lato",sans-serif;color:var(--ink);background:#fff;position:relative}
.heading{font-family:"Cabin",sans-serif;font-weight:500;text-transform:uppercase;letter-spacing:.5px}

.topbar{height:42px;background:var(--topbar);color:#fff;font-size:13px;display:flex;justify-content:flex-end;align-items:center;gap:60px;padding-right:80px}
.topbar span{display:flex;align-items:center;gap:10px}

.site-header{height:93px;display:flex;align-items:center;padding:0 77px;border-bottom:1px solid var(--line)}
.brand{display:flex;align-items:center;gap:12px;font-family:"Cabin",sans-serif;font-weight:700;color:var(--blue-mid);font-size:19px;line-height:19px;text-transform:uppercase}
.brand-mark{width:34px;height:34px;border-radius:50%;background:var(--blue-soft)}
.main-nav{margin-left:auto;display:flex;gap:27px;font-size:13px;color:#555;text-transform:uppercase;align-items:center}
.main-nav .active{color:var(--teal-mid)}
.lang{margin-left:8px;background:var(--blue);color:#fff;width:72px;height:35px;border-radius:3px;display:flex;align-items:center;justify-content:center;gap:8px;font-size:13px}

.hero{height:552px;position:relative;background:linear-gradient(115deg,#4a4a4a 0%,#2a2a2a 45%,#3b3b3b 100%);text-align:center}
.hero-photo{position:absolute;inset:0}
.hero h1{position:absolute;top:322px;left:0;right:0;font-family:"Cabin",sans-serif;font-weight:700;font-size:40px;color:var(--teal-mid);letter-spacing:1px}
.hero p{position:absolute;top:262px;left:270px;right:270px;top:262px;color:#fff;font-size:17px;line-height:27px;top:260px;margin-top:8px}
.hero p{top:263px}

.services{height:699px;position:relative}
.services h2{position:absolute;top:736px;top:49px;left:0;right:0;text-align:center;color:var(--blue);font-size:35px}
.service{position:absolute;width:240px;text-align:center}
.service .icon{width:94px;height:94px;border-radius:50%;margin:0 auto;box-shadow:0 2px 10px rgba(0,0,0,.12);display:flex;align-items:center;justify-content:center;background:#fff}
.service h3{margin-top:38px;color:var(--teal-mid);font-size:18px}
.service p{margin-top:18px;font-size:13px;color:var(--muted);line-height:25px}

.welcome{height:499px;display:flex}
.welcome-photo{width:594px;background:linear-gradient(135deg,#d9dde0 0%,#b9c2c7 40%,#7c8b96 100%)}
.welcome-text{flex:1;background:linear-gradient(160deg,var(--teal) 0%,#0a9fba 55%,var(--blue) 100%);color:#fff;padding:72px 80px 0 80px}
.welcome-text h2{font-size:36px;line-height:48px;font-weight:500}
.welcome-text p{margin-top:30px;font-size:12.5px;line-height:25px}
.btn-light{display:inline-block;margin-top:30px;width:188px;height:52px;line-height:52px;text-align:center;background:#fff;color:var(--blue);font-family:"Cabin",sans-serif;font-weight:600;font-size:17px;border-radius:3px}

.patient-info{height:395px;position:relative}
.patient-info h2{position:absolute;left:80px;top:64px;color:var(--blue);font-size:35px}
.btn-grey{position:absolute;left:841px;top:59px;width:281px;height:51px;line-height:51px;text-align:center;background:#ececec;border-radius:3px;font-family:"Cabin",sans-serif;font-size:18px;color:#555;text-transform:uppercase}
.info-card{position:absolute;top:163px;width:239px;height:133px;background:#fff;box-shadow:0 2px 10px rgba(0,0,0,.1);padding:26px 18px 0 18px}
.info-card h3{font-size:17px;font-weight:400;color:#444}
.info-card p{margin-top:14px;font-size:12.5px;line-height:25px;color:var(--muted)}

.testimonials{height:454px;position:relative}
.testimonial-photo{position:absolute;left:80px;top:0;width:468px;height:450px;background:linear-gradient(160deg,#f0e6d6 0%,#d9c3a0 40%,#7a4fc0 100%);border-radius:2px}
.testimonials h2{position:absolute;left:683px;top:48px;color:var(--blue);font-size:35px}
.quote{position:absolute;left:683px;top:118px}
.testimonials .text{position:absolute;left:683px;top:140px;width:440px;font-size:15px;line-height:27px;color:#777}
.testimonials .name{position:absolute;left:683px;top:247px;color:var(--teal-mid);font-size:18px}
.testimonials .role{position:absolute;left:683px;top:282px;font-size:13px;color:var(--muted)}

.meet-us{height:448px;background:var(--grey-bg);position:relative}
.meet-us h2{position:absolute;top:52px;left:0;right:0;text-align:center;color:var(--blue);font-size:35px}
.member{position:absolute;top:134px;width:360px;text-align:center}
.avatar{width:144px;height:144px;border-radius:50%;margin:0 auto;background:linear-gradient(160deg,#d6cfc6 0%,#8c7a6b 60%,#3a3431 100%)}
.member h3{margin-top:40px;font-size:18px;color:#333;font-weight:500}
.member p{margin-top:16px;font-size:13px;color:var(--muted)}

.contact{height:720px;background:linear-gradient(180deg,var(--teal) 0%,#0aa3b2 45%,var(--blue) 100%);position:relative;color:#fff}
.contact h2{position:absolute;top:62px;left:0;right:0;text-align:center;font-size:35px}
.contact .lead{position:absolute;top:124px;left:0;right:0;text-align:center;font-size:15.5px;line-height:28px}
.form-panel{position:absolute;left:77px;top:230px;width:1045px;height:395px;background:#fff;border-radius:3px}
.field{position:absolute;height:52px;border:1px solid #ccc;border-radius:3px;font-size:13px;color:#666;padding:16px 16px}
.btn-submit{position:absolute;left:429px;top:265px;width:186px;height:50px;line-height:50px;text-align:center;background:#ececec;border-radius:3px;font-family:"Cabin",sans-serif;font-size:17px;color:#555;text-transform:uppercase}

.site-footer{height:237px;position:relative}
.reach{position:absolute;top:52px;display:flex;align-items:center;gap:20px}
.reach .circle{width:62px;height:62px;border-radius:50%;background:#f1f1f1;border:1px solid #ddd;display:flex;align-items:center;justify-content:center}
.reach .label{font-size:13px;color:#888;line-height:27px}
.footer-rule{position:absolute;left:77px;right:78px;top:156px;border-top:1px solid var(--line)}
.copyright{position:absolute;left:80px;top:190px;font-size:13px;color:#888}
.social{position:absolute;right:78px;top:188px;display:flex;gap:22px}
.social span{width:16px;height:16px;border-radius:50%;background:#555}
</style>
</head>
<body>

<div class="topbar">
  <span><svg width="16" height="16" viewBox="0 0 24 24"><path fill="#33a6d7" d="M6.6 10.8a15.1 15.1 0 0 0 6.6 6.6l2.2-2.2c.3-.3.7-.4 1-.2 1.1.4 2.3.6 3.6.6.6 0 1 .4 1 1V20c0 .6-.4 1-1 1A17 17 0 0 1 3 4c0-.6.4-1 1-1h3.5c.6 0 1 .4 1 1 0 1.3.2 2.5.6 3.6.1.3 0 .7-.2 1z"/></svg>555 204 3180</span>
  <span><svg width="18" height="14" viewBox="0 0 24 18"><path fill="#33a6d7" d="M2 0h20a2 2 0 0 1 2 2v14a2 2 0 0 1-2 2H2a2 2 0 0 1-2-2V2a2 2 0 0 1 2-2zm10 8 10-6H2z"/></svg>hello@brightarchclinic.example</span>
</div>

<header class="site-header">
  <div class="brand"><span class="brand-mark"></span><span>The Bright Arch<br>Clinic</span></div>
  <nav class="main-nav">
    <span class="active">Home</span><span>Meet us</span><span>Services</span><span>Patient info</span><span>Cases &amp; reviews</span><span>Blog</span><span>Contact</span>
    <span class="lang">EN <svg width="12" height="8" viewBox="0 0 12 8"><path d="M1 1l5 5 5-5" stroke="#fff" stroke-width="2" fill="none"/></svg></span>
  </nav>
</header>

<section class="hero">
  <div class="hero-photo" role="img" aria-label="Close-up of a patient smiling in the dental chair while a dentist examines her teeth"></div>
  <h1>“YOUR SMILE. OUR PASSION.”</h1>
  <p style="top:386px">With Northfield and Ashbury credentials that inspire confidence, we offer cosmetic dentistry, general dentistry and multi-specialty dental care.</p>
</section>

<section class="services">
  <h2 class="heading">Dental services</h2>
  <div class="service" style="left:78px;top:127px"><div class="icon"><svg width="36" height="40" viewBox="0 0 36 40"><path d="M9 3c-5 0-7 5-6 10 1 4 3 6 3 11 0 6 2 13 5 13s3-9 7-9 4 9 7 9 5-7 5-13c0-5 2-7 3-11 1-5-1-10-6-10-4 0-5 2-9 2S13 3 9 3z" fill="none" stroke="#444" stroke-width="1.8"/></svg></div><h3 class="heading">Cosmetic dentistry</h3><p>Lorem ipsum dolor sit amet,<br>consectetur adipiscing elit, sed do.</p></div>
  <div class="service" style="left:346px;top:127px"><div class="icon"><svg width="30" height="44" viewBox="0 0 30 44"><path d="M5 3h20c2 0 3 3 2 6l-3 4H6L3 9C2 6 3 3 5 3z" fill="none" stroke="#444" stroke-width="1.8"/><path d="M9 15h12M9 21h12M10 27h10M11 33h8M13 39h4" stroke="#444" stroke-width="1.8"/></svg></div><h3 class="heading">Implant dentistry</h3><p>Lorem ipsum dolor sit amet,<br>consectetur adipiscing elit, sed do.</p></div>
  <div class="service" style="left:614px;top:127px"><div class="icon"><svg width="46" height="30" viewBox="0 0 46 30"><rect x="3" y="4" width="40" height="22" rx="6" fill="none" stroke="#444" stroke-width="1.8"/><path d="M3 13h40M13 4v22M23 4v22M33 4v22" stroke="#444" stroke-width="1.8"/></svg></div><h3 class="heading">Orthodontics</h3><p>Lorem ipsum dolor sit amet,<br>consectetur adipiscing elit, sed do.</p></div>
  <div class="service" style="left:884px;top:127px"><div class="icon"><svg width="44" height="36" viewBox="0 0 44 36"><rect x="3" y="3" width="38" height="12" rx="5" fill="none" stroke="#444" stroke-width="1.8"/><rect x="3" y="21" width="38" height="12" rx="5" fill="none" stroke="#444" stroke-width="1.8"/><path d="M12 3v12M22 3v12M32 3v12M12 21v12M22 21v12M32 21v12" stroke="#444" stroke-width="1.8"/></svg></div><h3 class="heading">Pediatric dentistry</h3><p>Lorem ipsum dolor sit amet,<br>consectetur adipiscing elit, sed do.</p></div>

  <div class="service" style="left:78px;top:408px"><div class="icon"><svg width="44" height="40" viewBox="0 0 44 40"><path d="M5 38C3 20 10 4 22 4s19 16 17 34" fill="none" stroke="#444" stroke-width="2"/><path d="M11 38C10 24 14 11 22 11s12 13 11 27" fill="none" stroke="#444" stroke-width="2"/></svg></div><h3 class="heading">Invisalign</h3><p>Lorem ipsum dolor sit amet,<br>consectetur adipiscing elit, sed do.</p></div>
  <div class="service" style="left:346px;top:408px"><div class="icon"><svg width="50" height="32" viewBox="0 0 50 32"><path d="M2 8h46M8 8v6h34V8" fill="none" stroke="#444" stroke-width="1.8"/><path d="M15 16c0 8 3 14 6 14s2-6 4-6 1 6 4 6 6-6 6-14" fill="none" stroke="#444" stroke-width="1.8"/></svg></div><h3 class="heading">Cleaning&amp;Prevention</h3><p>Lorem ipsum dolor sit amet,<br>consectetur adipiscing elit, sed do.</p></div>
  <div class="service" style="left:614px;top:408px"><div class="icon"><svg width="40" height="42" viewBox="0 0 40 42"><path d="M6 14c-4 0-5 4-4 8s2 5 2 9c0 5 1 9 3 9s2-6 5-6 3 6 5 6 3-4 3-9c0-4 1-5 2-9 1-4 0-8-4-8-3 0-4 1-6 1s-3-1-6-1z" fill="none" stroke="#444" stroke-width="1.8"/><circle cx="29" cy="11" r="8" fill="none" stroke="#444" stroke-width="1.8"/><path d="M29 7v8M25 11h8" stroke="#444" stroke-width="1.8"/></svg></div><h3 class="heading">Multi-speciality</h3><p>Lorem ipsum dolor sit amet,<br>consectetur adipiscing elit, sed do.</p></div>
  <div class="service" style="left:884px;top:408px"><div class="icon"><svg width="46" height="34" viewBox="0 0 46 34"><rect x="3" y="3" width="40" height="28" rx="10" fill="none" stroke="#444" stroke-width="1.8"/><path d="M3 17h40M13 5v24M23 3v28M33 5v24" stroke="#444" stroke-width="1.8"/></svg></div><h3 class="heading">Removable dentures</h3><p>Lorem ipsum dolor sit amet,<br>consectetur adipiscing elit, sed do.</p></div>
</section>

<section class="welcome">
  <div class="welcome-photo" role="img" aria-label="Smiling young woman seated in a blue dental chair"></div>
  <div class="welcome-text">
    <h2 class="heading">Welcome to The Bright Arch Clinic</h2>
    <p>Welcome to The Bright Arch Clinic where we specialize in General and Cosmetic Dentistry, Dental Implants, Periodontics (Gum Surgery), Endodontics (Root Canal Treatment) and Reconstructive Dentistry for patients in Boston, Brookline, Cambridge, Brighton, Allston, Newton, Watertown, Wellesley and all other surrounding neighborhoods of Boston, Massachusetts.</p>
    <span class="btn-light heading">Know more</span>
  </div>
</section>

<section class="patient-info">
  <h2 class="heading">Patient info</h2>
  <span class="btn-grey">Request appointment</span>
  <div class="info-card" style="left:77px"><h3>New Patient offer</h3><p>Lorem ipsum dolor sit amet,<br>consectetur adipiscing elit, sed.</p></div>
  <div class="info-card" style="left:345px"><h3>Accepted Insurance</h3><p>Lorem ipsum dolor sit amet,<br>consectetur adipiscing elit, sed.</p></div>
  <div class="info-card" style="left:615px"><h3>Patient portal</h3><p>Lorem ipsum dolor sit amet,<br>consectetur adipiscing elit, sed.</p></div>
  <div class="info-card" style="left:883px"><h3>Helpful tips</h3><p>Lorem ipsum dolor sit amet,<br>consectetur adipiscing elit, sed.</p></div>
</section>

<section class="testimonials">
  <div class="testimonial-photo" role="img" aria-label="Smiling blonde woman in a purple top holding a green apple"></div>
  <h2 class="heading">Testimonials</h2>
  <svg class="quote" width="56" height="44" viewBox="0 0 56 44"><path d="M22 4C10 8 4 16 4 26c0 8 5 13 11 13 5 0 9-4 9-9s-4-9-9-9c-2 0-3 0-4 1 1-6 5-11 12-14zM50 4C38 8 32 16 32 26c0 8 5 13 11 13 5 0 9-4 9-9s-4-9-9-9c-2 0-3 0-4 1 1-6 5-11 12-14z" fill="none" stroke="#999" stroke-width="1.5"/></svg>
  <p class="text" style="top:186px">Lorem ipsum dolor sit amet, consectetur adipiscing elit, s do eiusmod tempor incididunt ut labore et dolore magna aliqu. Ut enim ad minim veniam, quis nostrud.</p>
  <div class="name heading" style="top:292px">Name Surname</div>
  <div class="role" style="top:330px">Lorem ipsum dolor sit amet.</div>
</section>

<section class="meet-us">
  <h2 class="heading">Meet us</h2>
  <div class="member" style="left:58px"><div class="avatar" role="img" aria-label="Portrait of the orthodontist"></div><h3 class="heading">Lena Morrow, DMD, MS</h3><p>Board Certified Orthodontist</p></div>
  <div class="member" style="left:419px"><div class="avatar" role="img" aria-label="Portrait of the orthodontist"></div><h3 class="heading">Victor H. Lindqvist, DMD</h3><p>Board Certified Orthodontist</p></div>
  <div class="member" style="left:780px"><div class="avatar" role="img" aria-label="Portrait of the general dentist"></div><h3 class="heading">Dr. Nadia Fares, DMD</h3><p>General Dentist</p></div>
</section>

<section class="contact">
  <h2 class="heading">Get in touch</h2>
  <p class="lead">Lorem ipsum dolor sit amet, consectetur adipiscing elit, s do eiusmod tempor<br>incididunt ut labore et dolore magna aliqu. Ut enim ad minim veniam, quis nostrud.</p>
  <div class="form-panel">
    <div class="field" style="left:64px;top:72px;width:292px">Name</div>
    <div class="field" style="left:377px;top:72px;width:291px">Email</div>
    <div class="field" style="left:689px;top:72px;width:291px">Phone</div>
    <div class="field" style="left:64px;top:146px;width:916px;height:103px">Message</div>
    <span class="btn-submit">Submit</span>
  </div>
</section>

<footer class="site-footer">
  <div class="reach" style="left:77px"><span class="circle"><svg width="18" height="18" viewBox="0 0 24 24"><path fill="#666" d="M6.6 10.8a15.1 15.1 0 0 0 6.6 6.6l2.2-2.2c.3-.3.7-.4 1-.2 1.1.4 2.3.6 3.6.6.6 0 1 .4 1 1V20c0 .6-.4 1-1 1A17 17 0 0 1 3 4c0-.6.4-1 1-1h3.5c.6 0 1 .4 1 1 0 1.3.2 2.5.6 3.6.1.3 0 .7-.2 1z"/></svg></span><span class="label">CALL US<br>555.310.7421</span></div>
  <div class="reach" style="left:440px"><span class="circle"><svg width="18" height="14" viewBox="0 0 24 18"><path fill="#666" d="M2 0h20a2 2 0 0 1 2 2v14a2 2 0 0 1-2 2H2a2 2 0 0 1-2-2V2a2 2 0 0 1 2-2zm10 8 10-6H2z"/></svg></span><span class="label">EMAIL US<br>hello@brightarchclinic.example</span></div>
  <div class="reach" style="left:801px"><span class="circle"><svg width="16" height="20" viewBox="0 0 16 22"><path fill="#666" d="M8 0a8 8 0 0 1 8 8c0 6-8 14-8 14S0 14 0 8a8 8 0 0 1 8-8zm0 5a3 3 0 1 0 0 6 3 3 0 0 0 0-6z"/></svg></span><span class="label">270 Linden Avenue, Suite<br>12, Brookline MA 02446</span></div>
  <div class="footer-rule"></div>
  <div class="copyright">©THE BRIGHT ARCH CLINIC- 2019. All Rights Reserved.</div>
  <div class="social"><span aria-label="Social profile"></span><span aria-label="Social profile"></span><span aria-label="Social profile"></span></div>
</footer>

</body>
</html>
```